Soy Candle Labels

We sell soy candles in recycled wine bottles. The wine bottle is cut in half and filled with pure and natural soy wax and scented with essential oils.
Our product represents good use of up cycling materials for a better use. The product is all natural and eco friendly.
You can see good use of labels and branding for a company in America that does the same thing http://larkmeadow7wicks.example/
Trya dn keep the label uncomplicated like the above labels.
We will need an area to hand stamp the scent. Similar to the labels used on the above website.
We would prefer to use a white or off white paper label with gold or bronze printing - limit the use of colour and keep the label simple and sophisticated.
Emberlace Candle Co. is our company name. Emberlace being the predominant name and candle co. written small underneath right justified.
Die cut labels might look better than a rectangle.
Dimensions should be 90mm Wide x 90mm High
The final design should communicate a professional and quality product. But stay modern and professional. Clean, elegant and sophisticated.
Can use wording such as: Hand Poured, Premium Soy Wax, All Natural, Up cycled
Have a look at the attached image for the look and feel we are going for.
Updates
Designers are having a little bit of trouble interpreting the brief into a viable design. To assist perhaps you can look at WINE LABELS on google images. Design your label around an existing style wine label to give the canld ethe feel of being a bottle of wine. Get creative! :)
Reason: We require more designs. We havnt quite got what were looking for.
Please see brief.

```html
<!DOCTYPE html>
<html lang="en">
<head>
<meta charset="utf-8">
<title>Emberlace Candle Co. — Soy Candle Label</title>
<link href="https://fonts.googleapis.com/css2?family=Bai+Jamjuree:wght@400;500&family=Pathway+Gothic+One&display=swap" rel="stylesheet">
<style>
  :root {
    --backdrop: #3a1d10;
    --paper: #fdfcf6;
    --ink: #3d1e10;
  }
  * { margin: 0; padding: 0; box-sizing: border-box; }
  html, body {
    width: 1200px;
    height: 1000px;
    overflow: hidden;
    background: var(--backdrop);
  }
  .canvas {
    position: relative;
    width: 1200px;
    height: 1000px;
    background: var(--backdrop);
    font-family: "Bai Jamjuree", sans-serif;
    color: var(--ink);
  }
  .label {
    position: absolute;
    left: 130px;
    top: 35px;
    width: 932px;
    height: 932px;
    background: var(--paper);
    border-radius: 22px;
  }
  .label__frame {
    position: absolute;
    left: 17px;
    top: 17px;
    width: 899px;
    height: 898px;
    border: 1.2px solid var(--ink);
    border-radius: 16px;
  }
  .claims {
    position: absolute;
    left: 46px;
    top: 44px;
    line-height: 1;
  }
  .claims__title {
    font-size: 40px;
    font-weight: 500;
    margin-bottom: 10px;
  }
  .claims__line {
    font-size: 28px;
    font-weight: 400;
    margin-bottom: 9px;
  }
  .scent-stamp {
    position: absolute;
    left: 660px;
    top: 42px;
    width: 226px;
    height: 226px;
    border: 1px solid var(--ink);
    border-radius: 50%;
  }
  .scent-stamp__word {
    position: absolute;
    left: 42px;
    top: 28px;
    width: 26px;
    font-size: 27px;
    line-height: 31px;
    text-align: center;
    font-weight: 400;
  }
  .brand {
    position: absolute;
    right: 52px;
    top: 430px;
    text-align: right;
    line-height: 1;
  }
  .brand__name {
    font-size: 140px;
    font-weight: 400;
    letter-spacing: -2px;
  }
  .brand__sub {
    font-size: 34px;
    font-weight: 400;
    margin-top: 14px;
    margin-right: 25px;
  }
  .footer-note {
    position: absolute;
    top: 822px;
    font-family: "Pathway Gothic One", sans-serif;
    font-size: 50px;
    line-height: 1;
  }
  .footer-note--origin { left: 46px; }
  .footer-note--material { right: 45px; }
</style>
</head>
<body>
<main class="canvas">
  <section class="label">
    <div class="label__frame"></div>

    <div class="claims">
      <p class="claims__title">Hand Poured</p>
      <p class="claims__line">All Natural Soy</p>
      <p class="claims__line">320 gm of Premium Soy Wax</p>
    </div>

    <div class="scent-stamp">
      <p class="scent-stamp__word">S<br>C<br>E<br>N<br>T</p>
    </div>

    <div class="brand">
      <p class="brand__name">Emberlace</p>
      <p class="brand__sub">Candle Co.</p>
    </div>

    <p class="footer-note footer-note--origin">Product of Australia</p>
    <p class="footer-note footer-note--material">Up-Cycled wine bottle</p>
  </section>
</main>
</body>
</html>
```